4th Generation Family Business Needs a New Card Design!

We are a family owned 4th Generation company. We are based in the Sydney, Australia area and we are desperately in need of a more modern and classy card. We are monumental masons who design, supply & erect lasting memorials throughout cemeteries in Sydney. Our customers are normally in a period of grieving. I have attached logo files that will need to be implemented on the card. Company was established 1935. Australian Owned and Operated. Card needs to be designed to PIXO.com specification.

Target Market(s)

Our target market is based upon people that a grieving for family members that have passed away. We also deal with alot of companies that own and operate cemeteries.

Industry/Entity Type

Business

Contact Information for Business Card

Simon Harcourt, Operations Manager, 0417293086, simon@harcourtmemorials.com.au
Lewis Harcourt, Director, 0491630572, lewis@harcourtmemorials.com.au
Phone # 02 9561 3048
Website: www.harcourtmemorials.com.au
Address: Suite 17, 8 Palfrey Lane, West Carlow, Sydney NSW 2156

Font styles to use
Serif
Decorative
Script

Requirements
Must have
• Would like to see the logo nicely implemented with a modern design. Embossed lettering would be a nice additive.

```html
<!DOCTYPE html>
<html lang="en">
<head>
<meta charset="utf-8">
<title>Harcourt Memorials – Business Card</title>
<link rel="stylesheet" href="https://fonts.googleapis.com/css2?family=Cinzel:wght@600&family=Roboto:wght@400&display=swap">
<style>
  :root {
    --backdrop: #e9e7e4;
    --card-dark: #1f1f1f;
    --card-black: #121212;
    --card-white: #ffffff;
    --gold: #e2b523;
    --text-light: #d8d8d8;
    --ink: #222222;
    --emboss: #3a3a3a;
  }
  * { margin: 0; padding: 0; box-sizing: border-box; }
  html, body { width: 1200px; height: 716px; overflow: hidden; }
  body {
    background: var(--backdrop);
    display: flex;
    align-items: center;
    justify-content: center;
    gap: 40px;
    font-family: "Roboto", Arial, sans-serif;
  }
  .card {
    width: 540px;
    height: 310px;
    position: relative;
    overflow: hidden;
    box-shadow: 0 6px 18px rgba(0,0,0,0.18);
  }
  .card-front { display: flex; }
  .contact-panel {
    width: 236px;
    background: var(--card-dark);
    color: var(--text-light);
    position: relative;
    padding: 34px 0 0 26px;
    font-size: 11px;
    line-height: 1.55;
  }
  .accent-bar {
    position: absolute;
    left: 12px;
    top: 38px;
    width: 4px;
    height: 52px;
    background: var(--gold);
  }
  .person-name {
    font-family: "Cinzel", Georgia, serif;
    font-weight: 600;
    color: var(--gold);
    font-size: 15px;
    letter-spacing: 0.5px;
    line-height: 1.2;
  }
  .person-title { font-size: 11px; margin-bottom: 1px; }
  .contact-line { display: flex; align-items: center; gap: 5px; white-space: nowrap; }
  .contact-line svg { width: 9px; height: 9px; fill: var(--gold); flex: none; }
  .company-details {
    position: absolute;
    left: 26px;
    bottom: 30px;
  }
  .company-details .address { margin-bottom: 4px; }
  .brand-panel {
    flex: 1;
    background: var(--card-white);
    display: flex;
    align-items: center;
    justify-content: center;
  }
  .brand-lockup {
    display: flex;
    align-items: center;
    gap: 14px;
  }
  .brand-square {
    width: 46px;
    height: 46px;
    background: var(--ink);
    flex: none;
  }
  .brand-name {
    font-family: "Cinzel", Georgia, serif;
    font-weight: 600;
    font-size: 24px;
    line-height: 1.15;
    letter-spacing: 1px;
    color: var(--ink);
  }
  .card-back {
    background: var(--card-black);
    display: flex;
    align-items: center;
    justify-content: center;
  }
  .card-back .brand-square { background: var(--emboss); width: 56px; height: 56px; }
  .card-back .brand-name { color: var(--emboss); font-size: 30px; }
</style>
</head>
<body>
  <section class="card card-front" aria-label="Business card front">
    <div class="contact-panel">
      <span class="accent-bar"></span>
      <p class="person-name">Simon Harcourt</p>
      <p class="person-title">Operations Manager</p>
      <p class="contact-line">
        <svg viewBox="0 0 10 10" aria-hidden="true"><path d="M2.5 0h5a1 1 0 0 1 1 1v8a1 1 0 0 1-1 1h-5a1 1 0 0 1-1-1V1a1 1 0 0 1 1-1zm.5 1.5v6h4v-6z"/></svg>
        0417293086
      </p>
      <p class="contact-line">
        <svg viewBox="0 0 10 10" aria-hidden="true"><path d="M0 2h10v6H0zM.8 2.6 5 5.6l4.2-3z" fill-rule="evenodd"/></svg>
        simon@harcourtmemorials.com.au
      </p>
      <div class="company-details">
        <p class="address">Suite 17, 8 Palfrey Lane, West Carlow,<br>Sydney NSW 2156</p>
        <p class="contact-line">
          <svg viewBox="0 0 10 10" aria-hidden="true"><path d="M2 .5 3.8 2.8 2.8 4a6 6 0 0 0 3.2 3.2l1.2-1L9.5 8 8.3 9.5C4.5 9.3.7 5.5.5 1.7z"/></svg>
          02 9561 3048
        </p>
        <p class="contact-line">
          <svg viewBox="0 0 10 10" aria-hidden="true"><circle cx="5" cy="5" r="4.3" fill="none" stroke="#e2b523" stroke-width="1"/><path d="M.7 5h8.6M5 .7c-2.4 2.4-2.4 6.2 0 8.6M5 .7c2.4 2.4 2.4 6.2 0 8.6" fill="none" stroke="#e2b523" stroke-width=".8"/></svg>
          www.harcourtmemorials.com.au
        </p>
      </div>
    </div>
    <div class="brand-panel">
      <div class="brand-lockup">
        <span class="brand-square" aria-hidden="true"></span>
        <p class="brand-name">Harcourt<br>Memorials</p>
      </div>
    </div>
  </section>

  <section class="card card-back" aria-label="Business card back">
    <div class="brand-lockup">
      <span class="brand-square" aria-hidden="true"></span>
      <p class="brand-name">Harcourt<br>Memorials</p>
    </div>
  </section>
</body>
</html>
```